TavenLaw a fully remote and fully bilingual law firm for the Florida injured

1. Can you describe what your company does?- a solo lawyer practice in Florida, D.C., and soon in NY. I offer services for auto accidents, negligence, boat accident, motorcycle accident, insurance claims, premises liability, and things of the like.

2. Who are your target customers for the website? Drivers, passengers, pedestrians involved in accidents where they were injured and need help making a claim against the other vehicle or insurance company- throughout the entire state of Florida, but primarily in greater central florida area for english speaking and latino community offering a 100% bilingual services ENGLISH/SPANISH and 100% remote, where I wont make clients come to an office ever, and will private online meetings, signing portals, and all to have it efficient for clients benefit.

3. Do you have an existing domain name / website address? yes, tavenlaw.com through zentrova workspace. i need help in getting in brought to you so you can handle it please.

4. In addition to a Home Page, which other pages / sections would you like your website to have:
About Us
Contact Us
Products / Services
Office / Mailing Address
Testimonials / Reviews
FAQs
Terms and Conditions
Any other page / section you would like- DO EVERYTHING IN BOTH LANGUAGES- ENGLISH AND SPANISH
I want the page to have a way for people to calendar appts with me. and also
to make transactions - accepting all methods of payment

For each of the pages / sections you’d like to have, please provide the text (and images, if available) you would like to include.

5. Which of the below are features and functionalities your website will need:
Image Gallery
Videos
Contact Form
Mailing List
Maps
FAQs
Accepting payments / donations
6. Please provide the URLs for the social media profiles you'd like to link to the website. I have none, I am just starting, I actually want to have the online presence ready before my official launch.

Injured individuals by the negligent act of another in Florida

LAWYER/ AUTO ACCIDENT/NEGLIGENCE/ PREMISES LIABILITY/ CIVIL LAW

Coded - Design and coding required

1 page

• bilingual ENGLISH and SPANISH; a button for people to calendar appointments with me; accept payments, and to be able to integrate with major software like docusign, adobe, etc since I need to integrate under the fully remote platform
• look at my logo from artkiln.com it has the Tavenbrook Law and TavenLaw.com together.. I have the tavenlaw.com domain from zentrova. need you guys to help integrate that too , meaning to be able to use that domain for my website.

```html
<!DOCTYPE html>
<html lang="en">
<head>
<meta charset="utf-8">
<title>Tavenbrook Law — Personal Injury Legal Representation</title>
<link href="https://fonts.googleapis.com/css2?family=Cinzel:wght@400;500&family=Oswald:wght@400;500&family=Poppins:ital,wght@0,400;0,500;0,600;1,400&display=swap" rel="stylesheet">
<style>
:root{
  --navy:#1a2b52;
  --navy-deep:#14223f;
  --faq-blue:#1e3c70;
  --gold:#c9a03d;
  --gold-dark:#b58d2e;
  --ink:#222;
  --muted:#555;
  --light:#f1f1f1;
  --white:#fff;
  --black:#0b0b0b;
}
*{box-sizing:border-box;margin:0;padding:0}
html,body{width:1200px;height:5362px;overflow:hidden}
body{font-family:"Poppins",sans-serif;color:var(--ink);background:var(--white);position:relative;font-size:13px}
.abs{position:absolute}
.section-title{font-family:"Oswald",sans-serif;font-weight:500;letter-spacing:4px;font-size:34px;text-align:center;color:var(--navy)}
.title-rule{width:50px;height:2px;background:var(--gold);margin:14px auto 0}
.btn{display:inline-flex;align-items:center;gap:8px;background:var(--gold);color:var(--white);border-radius:30px;font-size:14px;font-weight:500;padding:0 24px;height:44px}
.btn svg{width:14px;height:10px}

/* hero */
.hero{position:absolute;left:0;top:0;width:1200px;height:640px;background:linear-gradient(180deg,#1b2a48 0%,#2c3c5e 45%,#3f5273 100%);overflow:hidden}
.hero-photo{position:absolute;left:560px;top:80px;width:390px;height:530px;background:radial-gradient(ellipse at 50% 35%,#7d6a5c 0%,#44506d 45%,#2d4c8f 75%,#2a437a 100%);border-radius:180px 180px 0 0;opacity:.9}
.nav-logo{position:absolute;left:70px;top:14px;width:220px;text-align:center;color:var(--white)}
.logo-circle{width:72px;height:72px;border:2px solid var(--white);border-radius:50%;margin:0 auto 10px}
.logo-name{font-family:"Poppins",sans-serif;font-weight:500;letter-spacing:5px;font-size:17px;text-transform:uppercase}
.nav{position:absolute;left:362px;top:30px;display:flex;gap:26px;color:var(--white);font-size:13px}
.lang{position:absolute;left:857px;top:24px;width:80px;height:26px;border:1px solid var(--white);border-radius:14px;color:var(--white);font-size:11px;display:flex;align-items:center;justify-content:center}
.call{position:absolute;left:968px;top:18px;display:flex;align-items:center;gap:12px;color:var(--white)}
.call-icon{width:38px;height:38px;border-radius:50%;background:var(--gold);display:flex;align-items:center;justify-content:center}
.call small{display:block;font-size:12px}
.call b{font-size:18px;font-weight:600;letter-spacing:1px}
.hero-title{position:absolute;left:72px;top:208px;border-left:2px solid var(--gold);padding-left:12px;font-family:"Cinzel",serif;color:var(--white);font-size:40px;line-height:50px;text-transform:uppercase}
.hero-text{position:absolute;left:72px;top:366px;width:430px;color:var(--white);font-size:13.5px;line-height:22px}
.hero .btn{position:absolute;left:72px;top:460px}
.hero-curve{position:absolute;left:0;top:560px;width:1200px;height:90px}
.scroll-down{position:absolute;left:570px;top:622px;width:60px;height:60px;border-radius:50%;background:var(--white);box-shadow:0 4px 14px rgba(0,0,0,.18);display:flex;align-items:center;justify-content:center}

/* services */
.services{position:absolute;top:700px;left:0;width:1200px;height:843px}
.services .section-title{margin-top:42px}
.intro{text-align:center;font-size:14px;line-height:26px;color:var(--muted);margin:22px auto 0;width:620px}
.card-grid{position:absolute;left:141px;top:198px;display:grid;grid-template-columns:repeat(3,286px);gap:30px 30px}
.card{height:219px;background:var(--white);box-shadow:0 3px 14px rgba(0,0,0,.1);padding:28px 28px}
.card.active{background:var(--navy);outline:2px solid var(--white);outline-offset:-8px;color:var(--white)}
.card-icon{width:58px;height:54px;border:2px solid var(--navy);border-radius:8px;margin-bottom:22px}
.card.active .card-icon{border-color:var(--white)}
.card h3{font-size:15px;font-weight:600;margin-bottom:8px}
.card p{font-size:12.5px;line-height:21px;color:var(--muted)}
.card.active p{color:#dde}
.more{display:inline-block;margin-top:10px;color:var(--gold);font-size:12.5px}
.services .btn{position:absolute;left:465px;top:700px}

/* why choose */
.why{position:absolute;top:1543px;left:0;width:1200px;height:626px;background:var(--navy)}
.why .section-title{color:var(--white);margin-top:62px}
.why-ring{position:absolute;left:458px;top:168px;width:284px;height:284px;border:3px solid var(--white);border-radius:50%;display:flex;flex-direction:column;align-items:center;justify-content:center;color:var(--white)}
.why-ring .logo-circle{width:70px;height:70px;margin-bottom:12px}
.feat{position:absolute;display:flex;align-items:center;gap:16px;color:var(--white)}
.feat.left{text-align:right}
.feat h4{font-size:15px;font-weight:500}
.feat p{font-size:12.5px;line-height:20px;color:#dfe3ee}
.feat-icon{width:66px;height:66px;border-radius:50%;border:2px solid var(--white);flex:none}
.feat-icon.gold{background:var(--gold);border-color:var(--gold);box-shadow:0 0 0 4px rgba(201,160,61,.35)}
.why .btn{position:absolute;left:465px;top:497px}

/* about */
.about{position:absolute;top:2169px;left:0;width:1200px;height:628px}
.about-frame{position:absolute;left:140px;top:110px;width:430px;height:420px;border:2px solid var(--navy)}
.about-photo{position:absolute;left:156px;top:98px;width:430px;height:430px;background:linear-gradient(180deg,#e8e8e6 0%,#bfbcb8 45%,#3a3b44 100%)}
.about-copy{position:absolute;left:662px;top:132px;width:400px}
.about-copy h2{font-family:"Oswald",sans-serif;font-weight:500;font-size:34px;letter-spacing:4px;color:var(--navy)}
.about-copy .rule{width:50px;height:2px;background:var(--gold);margin:10px 0 22px}
.about-copy p{font-size:12.5px;line-height:23px;color:var(--muted);margin-bottom:12px}
.about-copy .btn{margin-top:12px}

/* testimonials */
.reviews{position:absolute;top:2797px;left:0;width:1200px;height:572px;background:var(--light)}
.reviews .section-title{margin-top:80px}
.review{position:absolute;width:286px;background:var(--white);box-shadow:0 3px 14px rgba(0,0,0,.08);padding:36px 28px 24px}
.quote-mark{position:absolute;top:-14px;left:210px;font-family:"Cinzel",serif;font-size:70px;line-height:70px;color:var(--gold)}
.review p{font-style:italic;font-size:12.5px;line-height:23px;color:var(--muted)}
.review h5{margin-top:20px;font-size:13px;font-weight:600}
.stars{color:var(--gold);letter-spacing:3px;font-size:14px}
.review .src{position:absolute;right:26px;bottom:24px;font-size:13px;font-weight:600;color:var(--navy)}
.arrow-btn{position:absolute;top:3102px;width:32px;height:32px;border-radius:50%;display:flex;align-items:center;justify-content:center}
.dots{position:absolute;top:3280px;left:560px;display:flex;gap:8px}
.dots i{width:7px;height:7px;border-radius:50%;background:#c6c6c6}
.dots i:first-child{background:var(--navy)}

/* awards */
.awards{position:absolute;top:3369px;left:0;width:1200px;height:347px}
.awards .section-title{margin-top:80px}
.award-row{position:absolute;left:141px;top:168px;display:flex;gap:14px}
.award{width:141px;height:94px;background:var(--white);box-shadow:0 3px 12px rgba(0,0,0,.1);display:flex;align-items:center;justify-content:center}

/* faq */
.faq{position:absolute;top:3716px;left:0;width:1200px;height:582px;background:var(--faq-blue);color:var(--white)}
.faq h2{font-family:"Cinzel",serif;font-weight:400;text-align:center;font-size:38px;margin-top:84px}
.faq .title-rule{margin-top:8px}
.faq .sub{text-align:center;font-size:14px;margin-top:22px}
.faq-item{position:absolute;left:244px;width:710px;border:1px solid #c9d2e6;padding:0 20px;font-size:13px}
.faq-item .q{display:flex;justify-content:space-between;align-items:center;height:48px;font-weight:500}
.faq-item .a{font-size:12.5px;line-height:24px;padding-bottom:14px;margin-top:-6px}
.faq-item .toggle{color:var(--gold);font-size:22px;font-weight:400}

/* contact */
.contact{position:absolute;left:247px;top:4382px;width:705px;height:453px;background:var(--gold);box-shadow:0 22px 26px -18px rgba(0,0,0,.35)}
.contact h2{font-family:"Oswald",sans-serif;font-weight:500;font-size:34px;letter-spacing:4px;text-align:center;color:var(--white);margin-top:50px}
.contact .title-rule{background:var(--white)}
.field{position:absolute;height:38px;background:var(--white);font-size:11px;color:#888;padding:0 12px;display:flex;align-items:center;justify-content:space-between}
.field.msg{align-items:flex-start;padding-top:10px}
.submit{position:absolute;left:275px;top:376px;width:155px;height:44px;border-radius:30px;background:var(--navy);color:var(--white);font-size:14px;display:flex;align-items:center;justify-content:center;gap:8px}

/* footer */
.footer{position:absolute;left:0;top:4880px;width:1200px;height:482px}
.footer-curve{position:absolute;left:0;top:0;width:1200px;height:80px}
.footer-body{position:absolute;left:0;top:58px;width:1200px;height:424px;background:var(--black);color:var(--white)}
.f-logo{position:absolute;left:70px;top:115px;width:220px;text-align:center}
.f-logo .logo-circle{width:78px;height:78px}
.social{position:absolute;left:80px;top:226px;display:flex;gap:6px}
.social span{font-size:10px;border:1px solid var(--white);border-radius:12px;padding:3px 8px}
.f-col{position:absolute;top:115px}
.f-col h4{font-family:"Oswald",sans-serif;font-weight:500;font-size:16px;letter-spacing:2px;margin-bottom:20px}
.f-col li{list-style:none;font-size:12.5px;line-height:28px}
.f-contact li{display:flex;gap:10px;line-height:19px;margin-bottom:14px}
.f-contact svg{flex:none;margin-top:2px}
.copyright{position:absolute;left:70px;top:390px;font-size:12px}
.pay{position:absolute;right:70px;top:384px;display:flex;gap:5px}
.pay span{font-size:9px;font-weight:600;background:var(--white);color:var(--navy);padding:4px 6px;border-radius:3px}
</style>
</head>
<body>

<header class="hero">
  <div class="abs" role="img" aria-label="Night-time city skyline in deep blue tones" style="inset:0;background:linear-gradient(180deg,rgba(20,32,60,.2),rgba(35,50,80,.5))"></div>
  <div class="hero-photo" role="img" aria-label="Portrait of the attorney in a blue suit and tie"></div>
  <div class="nav-logo"><div class="logo-circle"></div><div class="logo-name">Tavenbrook Law</div></div>
  <nav class="nav"><span>Home</span><span>About Us</span><span>Services</span><span>Testimonials</span><span>FAQ's</span><span>Contact Us</span></nav>
  <div class="lang">EN ▾</div>
  <div class="call">
    <div class="call-icon"><svg width="16" height="16" viewBox="0 0 24 24" fill="#fff"><path d="M6.6 10.8a15 15 0 0 0 6.6 6.6l2.2-2.2c.3-.3.7-.4 1-.2 1.1.4 2.3.6 3.6.6.6 0 1 .4 1 1V20c0 .6-.4 1-1 1A17 17 0 0 1 3 4c0-.6.4-1 1-1h3.5c.6 0 1 .4 1 1 0 1.3.2 2.5.6 3.6.1.3 0 .7-.2 1z"/></svg></div>
    <div><small>Call Us Today</small><b>123 456 7890</b></div>
  </div>
  <h1 class="hero-title">Expert Personal<br>Injury Legal<br>Representation</h1>
  <p class="hero-text">Bilingual legal services for auto accidents, negligence claims, and personal injury cases throughout Florida, DC, and soon NY. <b>100%</b> remote consultations available.</p>
  <span class="btn">Schedule Free Consultation <svg viewBox="0 0 14 10" fill="none" stroke="#fff" stroke-width="1.5"><path d="M0 5h12M8 1l4 4-4 4"/></svg></span>
</header>
<svg class="hero-curve" viewBox="0 0 1200 90" preserveAspectRatio="none" aria-hidden="true" style="position:absolute;top:560px;left:0">
  <path d="M0 36 Q600 90 1200 10 L1200 90 L0 90Z" fill="#fff"/>
  <path d="M0 36 Q600 90 1200 10" fill="none" stroke="#c9a03d" stroke-width="4"/>
</svg>
<div class="scroll-down"><svg width="22" height="12" viewBox="0 0 22 12" fill="none" stroke="#1a2b52" stroke-width="2"><path d="M1 1l10 10L21 1"/></svg></div>

<section class="services">
  <h2 class="section-title">OUR SERVICES</h2>
  <div class="title-rule"></div>
  <p class="intro">I offer services for auto accidents, negligence, boat accident, motorcycle accident, insurance claims, premises liability, and things of the like.</p>
  <div class="card-grid">
    <article class="card active"><div class="card-icon" role="img" aria-label="Auto accident icon"></div><h3>Auto Accident</h3><p>Duis autem vel eum iriure dolor inm hendrerit in vulputate.</p><span class="more">Read More →</span></article>
    <article class="card"><div class="card-icon" role="img" aria-label="Negligence icon"></div><h3>Negligence</h3><p>Duis autem vel eum iriure dolor inm hendrerit in vulputate.</p><span class="more">Read More →</span></article>
    <article class="card"><div class="card-icon" role="img" aria-label="Boat accident icon"></div><h3>Motorcycle Accident</h3><p>Duis autem vel eum iriure dolor inm hendrerit in vulputate.</p><span class="more">Read More →</span></article>
    <article class="card"><div class="card-icon" role="img" aria-label="Motorcycle accident icon"></div><h3>Motorcycle Accident</h3><p>Duis autem vel eum iriure dolor inm hendrerit in vulputate.</p><span class="more">Read More →</span></article>
    <article class="card"><div class="card-icon" role="img" aria-label="Insurance claims icon"></div><h3>Insurance Claims</h3><p>Duis autem vel eum iriure dolor inm hendrerit in vulputate.</p><span class="more">Read More →</span></article>
    <article class="card"><div class="card-icon" role="img" aria-label="Premises injury icon"></div><h3>Motorcycle Accident</h3><p>Duis autem vel eum iriure dolor inm hendrerit in vulputate.</p><span class="more">Read More →</span></article>
  </div>
  <span class="btn">Schedule Free Consultation <svg viewBox="0 0 14 10" fill="none" stroke="#fff" stroke-width="1.5"><path d="M0 5h12M8 1l4 4-4 4"/></svg></span>
</section>

<section class="why">
  <h2 class="section-title">WHY CHOOSE US</h2>
  <div class="title-rule"></div>
  <div class="why-ring"><div class="logo-circle"></div><div class="logo-name">Tavenbrook Law</div></div>
  <div class="feat left" style="right:742px;top:166px"><div><h4>Millions Recovered</h4><p>Lorem ipsum dolor sit amet,<br>consectetuer adipiscing elit sed</p></div><div class="feat-icon gold" role="img" aria-label="Recovery icon"></div></div>
  <div class="feat left" style="right:742px;top:282px"><div><h4>100% bilingual services<br>ENGLISH/SPANISH</h4><p>Lorem ipsum dolor sit amet</p></div><div class="feat-icon" role="img" aria-label="Language icon"></div></div>
  <div class="feat left" style="right:742px;top:398px"><div><h4>Client-Focused Approach</h4><p>Lorem ipsum dolor sit amet,<br>consectetuer adipiscing elit sed</p></div><div class="feat-icon" role="img" aria-label="Client focus icon"></div></div>
  <div class="feat" style="left:742px;top:166px"><div class="feat-icon" role="img" aria-label="Success rate icon"></div><div><h4>99% Success Rate</h4><p>Lorem ipsum dolor sit amet,<br>consectetuer adipiscing elit sed</p></div></div>
  <div class="feat" style="left:776px;top:282px"><div class="feat-icon" role="img" aria-label="Remote service icon"></div><div><h4>100% Remote Service -<br>No Office Visits Required</h4><p>Lorem ipsum dolor sit amet</p></div></div>
  <div class="feat" style="left:742px;top:398px"><div class="feat-icon" role="img" aria-label="No fee icon"></div><div><h4>No-Fee Promise</h4><p>Lorem ipsum dolor sit amet,<br>consectetuer adipiscing elit sed</p></div></div>
  <span class="btn">Schedule Free Consultation <svg viewBox="0 0 14 10" fill="none" stroke="#fff" stroke-width="1.5"><path d="M0 5h12M8 1l4 4-4 4"/></svg></span>
</section>

<section class="about">
  <div class="about-frame"></div>
  <div class="about-photo" role="img" aria-label="Portrait of the attorney in a dark suit"></div>
  <div class="about-copy">
    <h2>ABOUT ME</h2>
    <div class="rule"></div>
    <p>I am a solo lawyer practice in Florida, D.C., and soon in NY. I offer services for auto accidents, negligence, boat accidents, motorcycle accidents, insurance claims, premises liability, and similar matters.</p>
    <p>Our target audience includes drivers, passengers, and pedestrians involved in accidents who need help making claims against other parties or insurance companies. We serve the entire state of Florida, primarily the greater central Florida area, for the English-speaking and Latino communities.</p>
    <span class="btn">Contact Me <svg viewBox="0 0 14 10" fill="none" stroke="#fff" stroke-width="1.5"><path d="M0 5h12M8 1l4 4-4 4"/></svg></span>
  </div>
</section>

<section class="reviews">
  <h2 class="section-title">WHAT OUR HAPPY CLIENTS SAY</h2>
  <div class="title-rule"></div>
  <article class="review" style="left:141px;top:182px;height:182px"><span class="quote-mark">“</span><p>“Duis autem vel eum iriure dolorm in hendrerit in vulputate velit essle molestie consequat, vel illu morel dolore eu nullam at verom eros et qui blandit praesent facilisis.”</p><h5>MARK DELANO</h5><div class="stars">★★★★★</div><span class="src">zentrova</span></article>
  <article class="review" style="left:457px;top:182px;height:230px"><span class="quote-mark">“</span><p>“Duis autem vel eum iriure dolorm in hendrerit in vulputate velit essle molestie consequat, vel illu morel dolore eu nullam at verom eros et accumsan et iusto odio dignissim qui blandit praesent facilisis.”</p><h5>MARK DELANO</h5><div class="stars">★★★★★</div><span class="src">zentrova</span></article>
  <article class="review" style="left:773px;top:182px;height:182px"><span class="quote-mark">“</span><p>“Duis autem vel eum iriure dolorm in hendrerit in vulputate velit essle molestie consequat, vel illu morel dolore eu nullam at verom eros et qui blandit praesent facilisis.”</p><h5>MARK DELANO</h5><div class="stars">★★★★★</div><span class="src">zentrova</span></article>
</section>
<div class="arrow-btn" style="left:64px;background:#d4d4d4"><svg width="8" height="12" viewBox="0 0 8 12" fill="none" stroke="#fff" stroke-width="2"><path d="M7 1L2 6l5 5"/></svg></div>
<div class="arrow-btn" style="left:1104px;background:var(--navy)"><svg width="8" height="12" viewBox="0 0 8 12" fill="none" stroke="#fff" stroke-width="2"><path d="M1 1l5 5-5 5"/></svg></div>
<div class="dots"><i></i><i></i><i></i><i></i><i></i><i></i></div>

<section class="awards">
  <h2 class="section-title">AWARDS &amp; ACCRIDATION</h2>
  <div class="title-rule"></div>
  <div class="award-row">
    <div class="award"><div role="img" aria-label="Award badge" style="width:100px;height:26px;background:#d9b3b3;border-radius:3px"></div></div>
    <div class="award"><div role="img" aria-label="Rating badge" style="width:56px;height:62px;background:var(--navy);border-radius:6px 6px 28px 28px"></div></div>
    <div class="award"><div role="img" aria-label="Association seal" style="width:62px;height:62px;background:#7a5a1c;border-radius:50%"></div></div>
    <div class="award"><div role="img" aria-label="Listing badge" style="width:76px;height:62px;background:#2f5fa8;border-radius:4px"></div></div>
    <div class="award"><div role="img" aria-label="Rating seal" style="width:62px;height:62px;border:4px solid #2f5fa8;border-radius:50%"></div></div>
    <div class="award"><div role="img" aria-label="Peer review badge" style="width:104px;height:26px;background:#c23a3a;border-radius:3px"></div></div>
  </div>
</section>

<section class="faq">
  <h2>FAQ's</h2>
  <div class="title-rule"></div>
  <p class="sub">Common questions about our services and process.</p>
  <div class="faq-item" style="top:202px"><div class="q">What areas do you serve?<span class="toggle">–</span></div><p class="a">Duis autem vel eum iriure dolorm in hendrerit in vulputate velit essle molestie consequat, vel illu morel dolore eu nullam at verom eros et accumsan et iusto odio dignissim qui blandit praesent facilisis.</p></div>
  <div class="faq-item" style="top:326px"><div class="q">Do I need to visit an office?<span class="toggle">+</span></div></div>
  <div class="faq-item" style="top:389px"><div class="q">How much do your services cost?<span class="toggle">+</span></div></div>
  <div class="faq-item" style="top:452px"><div class="q">How long do personal injury cases typically take?<span class="toggle">+</span></div></div>
</section>

<section class="contact">
  <h2>GET IN TOUCH</h2>
  <div class="title-rule"></div>
  <div class="field" style="left:40px;top:141px;width:300px">First name*<span>👤</span></div>
  <div class="field" style="left:365px;top:141px;width:300px">Last name*<span>👤</span></div>
  <div class="field" style="left:40px;top:196px;width:300px">Email*<span>✉</span></div>
  <div class="field" style="left:365px;top:196px;width:300px">Phone*<span>☎</span></div>
  <div class="field msg" style="left:40px;top:250px;width:625px;height:74px">Message<span>✎</span></div>
  <div class="submit">Submit Now <svg width="14" height="10" viewBox="0 0 14 10" fill="none" stroke="#fff" stroke-width="1.5"><path d="M0 5h12M8 1l4 4-4 4"/></svg></div>
</section>

<footer class="footer">
  <svg class="footer-curve" viewBox="0 0 1200 80" preserveAspectRatio="none" aria-hidden="true">
    <path d="M0 20 Q600 90 1200 40 L1200 80 L0 80Z" fill="#0b0b0b"/>
    <path d="M0 20 Q600 90 1200 40" fill="none" stroke="#c9a03d" stroke-width="4"/>
  </svg>
  <div class="footer-body">
    <div class="f-logo"><div class="logo-circle"></div><div class="logo-name">Tavenbrook Law</div></div>
    <div class="social"><span>Friendra</span><span>Quipper</span><span>Workly</span><span>Snapora</span></div>
    <div class="f-col" style="left:420px"><h4>QUICK LINKS</h4><ul><li>Home</li><li>About Us</li><li>Services</li><li>Testimonials</li><li>FAQ's</li><li>Contact Us</li></ul></div>
    <div class="f-col" style="left:627px"><h4>SERVICES</h4><ul><li>Auto Accidents</li><li>Negligence</li><li>Boat Accident</li><li>Motorcycle Accident</li><li>Insurance Claims</li><li>Premises Liability</li></ul></div>
    <div class="f-col f-contact" style="left:875px;width:270px"><h4>CONTACT DETAILS</h4><ul>
      <li><svg width="12" height="14" viewBox="0 0 12 14" fill="#c9a03d"><path d="M6 0a5 5 0 0 0-5 5c0 4 5 9 5 9s5-5 5-9a5 5 0 0 0-5-5zm0 7a2 2 0 1 1 0-4 2 2 0 0 1 0 4z"/></svg>123, Loream Ipsum Dollar Road, Florida. FL - 123 456</li>
      <li style="font-size:15px;font-weight:600;letter-spacing:1px"><svg width="13" height="13" viewBox="0 0 24 24" fill="#c9a03d"><path d="M6.6 10.8a15 15 0 0 0 6.6 6.6l2.2-2.2c.3-.3.7-.4 1-.2 1.1.4 2.3.6 3.6.6.6 0 1 .4 1 1V20c0 .6-.4 1-1 1A17 17 0 0 1 3 4c0-.6.4-1 1-1h3.5c.6 0 1 .4 1 1 0 1.3.2 2.5.6 3.6.1.3 0 .7-.2 1z"/></svg>(555) 123-4567</li>
      <li><svg width="13" height="10" viewBox="0 0 13 10" fill="#c9a03d"><path d="M0 0h13v10H0z M1 1l5.5 4L12 1" /></svg>info@tavenlaw.com</li>
      <li><svg width="13" height="13" viewBox="0 0 14 14" fill="none" stroke="#c9a03d" stroke-width="2"><circle cx="7" cy="7" r="6"/><path d="M7 3v4h3"/></svg>Monday - Friday: 9:00 AM - 6:00 PM<br>Weekends: By appointment only</li>
    </ul></div>
    <p class="copyright">© 2025 Tavenbrook Law. All rights reserved.</p>
    <div class="pay"><span>Ampora</span><span>Veltra</span><span>Corvid</span><span>Payvane</span><span>Sendra</span></div>
  </div>
</footer>

</body>
</html>
```